Website Re-design for Kids Playhouse Business

Need current website which looks very outdated to be re-designed to look modern and contemporary, reduce clutter significantly and make it look elegant and simple.
Current website: http://www.tumblenest.com.au/
A website which the business owner likes, use as reference/inspiration: http://vexa.com.au/
Looking for light green palette, natural colours. "WHAT'S ON" page/link no longer required.
Industry/Entity Type
Business
Number of Pages Required
5+ page
Look and feel
Each slider illustrates characteristics of the customer's brand and the style your logo design should communicate.

```html
<!DOCTYPE html>
<html lang="en">
<head>
<meta charset="utf-8">
<title>Tumble Nest Playhouse &amp; Cafe</title>
<link href="https://fonts.googleapis.com/css2?family=Open+Sans:wght@400;600;700&display=swap" rel="stylesheet">
<style>
:root{
  --green:#8ee01b;
  --green-panel:#9ef02a;
  --ink:#1d1d1d;
  --grey:#e6e6e6;
  --grey-dark:#d2d2d2;
  --white:#ffffff;
  --muted:#555555;
}
*{margin:0;padding:0;box-sizing:border-box}
html,body{width:1200px;height:2305px;overflow:hidden;background:var(--white)}
body{font-family:"Open Sans",Arial,sans-serif;color:var(--ink);position:relative}
.abs{position:absolute}
/* hero */
.hero{left:0;top:0;width:1200px;height:614px;background:linear-gradient(135deg,#9fc46a 0%,#e3b79a 40%,#c98e76 65%,#7fa555 100%)}
.hero-title{left:138px;top:512px;font-size:62px;font-weight:600;color:var(--white);letter-spacing:1px;white-space:nowrap;z-index:1}
.hero-arrow{top:292px;width:28px;height:28px;background:rgba(90,70,40,.6);display:flex;align-items:center;justify-content:center}
.brand{left:31px;top:43px;width:181px;height:89px;background:var(--white);border:3px solid #7a4a2a;display:flex;align-items:center;justify-content:center;gap:8px;font-size:20px;font-weight:700;color:#d2232a}
.brand-dot{width:12px;height:12px;border-radius:50%;background:#d2232a}
.nav-panel{left:920px;top:0;width:280px;height:614px;background:rgba(158,240,42,.9);z-index:2}
.nav-icon{top:21px;width:46px;height:46px;border-radius:50%;display:flex;align-items:center;justify-content:center}
.nav-icon.phone{left:137px;border:2px solid #b9f76a}
.nav-icon.close{left:209px;border:3px solid var(--white)}
.nav-list{list-style:none;position:absolute;right:33px;top:90px;text-align:right}
.nav-list li{font-size:19px;line-height:43px;color:#1f2a10}
/* welcome */
.welcome{left:25px;top:679px;width:268px;height:292px}
.welcome h1{font-size:20px;font-weight:700;line-height:28px;letter-spacing:-.2px}
.welcome p{margin-top:14px;font-size:10.5px;line-height:17px;color:var(--muted)}
.read-more{position:absolute;left:0;top:252px;font-size:16px;font-weight:700;display:flex;align-items:center;gap:8px}
.card{top:679px;width:212px;height:292px;background:var(--green)}
.card-image{height:140px}
.card h2{padding:16px 14px 0;font-size:20px;font-weight:600;line-height:27px;color:var(--white);letter-spacing:-.2px}
.card-link{position:absolute;left:14px;top:254px;font-size:15px;font-weight:700;color:var(--white);display:flex;align-items:center;gap:7px;white-space:nowrap}
/* testimonial */
.avatar{left:24px;top:1052px;width:252px;height:252px;border-radius:50%;background:radial-gradient(circle at 40% 45%,#e9b79c,#b94a3a 55%,#6b8a45)}
.quote-box{left:301px;top:1051px;width:873px;height:255px;background:var(--grey)}
.quote-box::before{content:"";position:absolute;left:-30px;top:22px;border-top:18px solid transparent;border-bottom:18px solid transparent;border-right:30px solid var(--grey)}
.quote-side{right:0;top:0;width:25px;height:255px;background:var(--grey-dark);display:flex;align-items:center;justify-content:center}
.quote-text{left:40px;top:24px;width:800px;font-size:24.5px;line-height:37px;color:#333}
.quote-name{left:40px;top:192px;font-size:21px;font-weight:700}
/* contact */
.contact{left:0;top:1389px;width:1200px;height:450px;background:linear-gradient(180deg,#eeeee9,#e4e2dc)}
.contact h2{position:absolute;top:66px;width:100%;text-align:center;font-size:41px;font-weight:400}
.contact .sub{position:absolute;top:126px;width:100%;text-align:center;font-size:16px;color:#333}
.field{height:48px;background:var(--green);color:#1d2a0a;font-size:14px;padding:0 22px;display:flex;align-items:center}
.captcha{gap:12px;padding:0 16px}
.captcha small{display:block;font-size:9px;line-height:11px}
.captcha b{font-size:15px}
.captcha-answer{right:0;top:0;width:64px;height:48px;background:#7ac314}
.send{left:531px;top:322px;width:136px;height:48px;background:#2b2b2b;color:var(--white);font-size:14px;font-weight:600;display:flex;align-items:center;justify-content:center;letter-spacing:.5px}
/* info */
.info{left:0;top:1839px;width:1200px;height:90px;display:flex;justify-content:space-between;align-items:center;padding:0 25px;font-size:16px}
.info span{display:flex;align-items:center;gap:8px;white-space:nowrap}
.map{left:0;top:1929px;width:1200px;height:272px;background:linear-gradient(160deg,#e6e4df,#dcdad4 60%,#e8e6e0)}
.footer{left:0;top:2227px;width:1200px;text-align:center;font-size:13px;color:#333}
.socials{left:0;top:2256px;width:1200px;display:flex;justify-content:center;gap:12px}
.socials i{width:26px;height:26px;border-radius:50%;display:block}
</style>
</head>
<body>

<section class="abs hero" role="img" aria-label="Photo of young children playing with colourful craft sticks at a table"></section>
<div class="abs hero-arrow" style="left:0"><svg width="14" height="14" viewBox="0 0 14 14"><path d="M12 7H3M7 3L3 7l4 4" stroke="#fff" stroke-width="2" fill="none"/></svg></div>
<div class="abs brand"><span class="brand-dot"></span>Tumble Nest</div>
<div class="abs hero-title">SO MUCH FUN FOR EVERYONE</div>

<nav class="abs nav-panel">
  <div class="abs nav-icon phone"><svg width="18" height="18" viewBox="0 0 24 24"><path d="M6 3l3 4-2 2c1 3 4 6 7 7l2-2 4 3-2 4C10 21 3 14 3 5z" fill="#b9f76a"/></svg></div>
  <div class="abs nav-icon close"><svg width="20" height="20" viewBox="0 0 20 20"><circle cx="10" cy="10" r="9" fill="#1d1d1d"/><path d="M6.5 6.5l7 7M13.5 6.5l-7 7" stroke="#fff" stroke-width="2.2"/></svg></div>
  <ul class="nav-list">
    <li>Home</li><li>Hours &amp; Prices</li><li>Party Packages</li><li>Party Rooms</li><li>Vacation Care</li><li>School Holiday Program</li><li>Specials &amp; Promotions</li><li>Gallery</li><li>Contact Us</li>
  </ul>
</nav>

<section class="abs welcome">
  <h1>Welcome to Tumble Nest, Sydney's newest and best party &amp; play centre!</h1>
  <p>Tumble Nest is an indoor Kids Play Centre and Cafe that offers both kids and adults a chance to enjoy their time, together! We pride ourselves in offering the best indoor play centre for your kids to engage in fun and learning activities in a specially created environment that is not only warm and safe but also enhances and stimulates creativity and curiosity in a child.</p>
  <div class="read-more"><svg width="15" height="15" viewBox="0 0 16 16"><circle cx="8" cy="8" r="8" fill="#1d1d1d"/><path d="M4 8h7M8 5l3 3-3 3" stroke="#fff" stroke-width="1.8" fill="none"/></svg>READ MORE</div>
</section>

<article class="abs card" style="left:301px"><div class="card-image" role="img" aria-label="Photo of a birthday party crowd around a cake" style="background:linear-gradient(135deg,#2e3a22,#8a5a3a)"></div><h2>Perfect venue for birthdays and private parties</h2><div class="card-link"><svg width="15" height="15" viewBox="0 0 16 16"><circle cx="8" cy="8" r="8" fill="#fff"/><path d="M4 8h7M8 5l3 3-3 3" stroke="#8ee01b" stroke-width="1.8" fill="none"/></svg>VIEW PARTIES</div></article>
<article class="abs card" style="left:522px"><div class="card-image" role="img" aria-label="Photo of a decorated party room with balloons" style="background:linear-gradient(135deg,#7a2a7a,#e05aa0)"></div><h2>4 Kids loving party rooms themes</h2><div class="card-link"><svg width="15" height="15" viewBox="0 0 16 16"><circle cx="8" cy="8" r="8" fill="#fff"/><path d="M4 8h7M8 5l3 3-3 3" stroke="#8ee01b" stroke-width="1.8" fill="none"/></svg>VIEW PARTY ROOMS</div></article>
<article class="abs card" style="left:743px"><div class="card-image" role="img" aria-label="Photo of costumed characters at a school holiday show" style="background:linear-gradient(135deg,#d9c22a,#c82a2a)"></div><h2>We host school holiday programs</h2><div class="card-link"><svg width="15" height="15" viewBox="0 0 16 16"><circle cx="8" cy="8" r="8" fill="#fff"/><path d="M4 8h7M8 5l3 3-3 3" stroke="#8ee01b" stroke-width="1.8" fill="none"/></svg>VIEW PROGRAMS</div></article>
<article class="abs card" style="left:963px"><div class="card-image" role="img" aria-label="Photo of a table set with teal cups and plates" style="background:linear-gradient(135deg,#3f5a52,#4ac0b8)"></div><h2>Exclusive specials &amp; promotions</h2><div class="card-link"><svg width="15" height="15" viewBox="0 0 16 16"><circle cx="8" cy="8" r="8" fill="#fff"/><path d="M4 8h7M8 5l3 3-3 3" stroke="#8ee01b" stroke-width="1.8" fill="none"/></svg>VIEW MORE</div></article>

<div class="abs avatar" role="img" aria-label="Round photo of a happy child playing"></div>
<blockquote class="abs quote-box">
  <p class="abs quote-text">“ Excellent place for kids and parents, amazing party rooms, friendly, fun and helpful staff! I highly recommend for hosting your next party or just to relax in air-con whilst watching your kids have a ball on the play equipment and activities! ”</p>
  <cite class="abs quote-name" style="font-style:normal">Mara Lin Cole</cite>
  <div class="abs quote-side"><svg width="10" height="16" viewBox="0 0 10 16"><path d="M2 2l6 6-6 6" stroke="#888" stroke-width="1.6" fill="none"/></svg></div>
</blockquote>

<section class="abs contact" role="region" aria-label="Contact form over a soft faded classroom photo">
  <h2>Contact Us</h2>
  <p class="sub">Our postal address and contact details</p>
  <div class="abs field" style="left:25px;top:179px;width:271px">Name</div>
  <div class="abs field" style="left:318px;top:179px;width:272px">Phone</div>
  <div class="abs field" style="left:610px;top:179px;width:272px">Email</div>
  <div class="abs field" style="left:903px;top:179px;width:272px">Postcode</div>
  <div class="abs field" style="left:25px;top:251px;width:857px">Message</div>
  <div class="abs field captcha" style="left:903px;top:251px;width:272px">
    <svg width="22" height="22" viewBox="0 0 24 24"><path d="M20 12a8 8 0 1 1-3-6.2" stroke="#1d1d1d" stroke-width="3" fill="none"/><path d="M14 3h6v6z" fill="#1d1d1d"/></svg>
    <div><small>Enter the answer to avoid spam</small><b>92 + 6 =</b></div>
    <div class="abs captcha-answer"></div>
  </div>
  <div class="abs send">SEND MESSAGE</div>
</section>

<div class="abs info">
  <span><svg width="12" height="16" viewBox="0 0 12 16"><path d="M6 0a6 6 0 0 1 6 6c0 4-6 10-6 10S0 10 0 6a6 6 0 0 1 6-6z" fill="#1d1d1d"/><circle cx="6" cy="6" r="2.2" fill="#fff"/></svg>41 Willow Lane Greenfield 2190 NSW Australia.</span>
  <span><svg width="14" height="14" viewBox="0 0 24 24"><path d="M6 3l3 4-2 2c1 3 4 6 7 7l2-2 4 3-2 4C10 21 3 14 3 5z" fill="#1d1d1d"/></svg>Ph:&nbsp; 02 9555 0148</span>
  <span><svg width="14" height="14" viewBox="0 0 16 16"><rect x="1" y="5" width="14" height="9" fill="#1d1d1d"/><rect x="4" y="1" width="8" height="5" fill="#1d1d1d"/><rect x="5" y="8" width="6" height="2" fill="#fff"/></svg>Fax: 02 9555 0149</span>
  <span><svg width="16" height="12" viewBox="0 0 16 12"><rect width="16" height="12" fill="#1d1d1d"/><path d="M0 0l8 6 8-6" stroke="#fff" stroke-width="1.4" fill="none"/></svg>Email:&nbsp; hello@tumblenestplay.com</span>
</div>

<div class="abs map" role="img" aria-label="Street map showing the playhouse location"></div>

<footer class="abs footer">Copyright &nbsp;©&nbsp; 2018 &nbsp;Tumble Nest. &nbsp;&nbsp;All rights reserved.</footer>
<div class="abs socials"><i style="background:#3b5998"></i><i style="background:#e0453a"></i></div>

</body>
</html>
```